New career and executive coaching business needs a business card design including logo

Company name: 'Bramblefield Growth Partners.' The aim of my coaching engagements is to help people improve their communication in the workplace and achieve their career goals. The process involves working with individuals to help them uncover their strengths and talents, then leverage those to improve their working lives. The Tarwick Inventory is the starting point to the process. I am after an exciting and interesting business card design (including logo)which is professional yet will still get people's attention.

Industry/Entity Type

Business

Contact Information for Business Card

Name: Malcolm Dervaney
Position: Owner
Address: 58 Quorrin Ct, Elmbridge Vic 3190
Phone: 0418923047
Website: bramblefieldgrowth.com.au
Email: malcolm@bgp.com.au

Colors
33a6d7
00a990
0355a3
3176b5

Requirements
Must have
• logo

```html
<!DOCTYPE html>
<html lang="en">
<head>
<meta charset="utf-8">
<title>Bramblefield Growth Partners – Business Card</title>
<link rel="stylesheet" href="https://fonts.googleapis.com/css2?family=Tinos:wght@400;700&family=Arimo:wght@400;500&display=swap">
<style>
  :root {
    --navy: #0355a3;
    --mid-blue: #3176b5;
    --sky: #33a6d7;
    --ink: #111111;
    --paper: #ffffff;
    --backdrop: #e9e9e9;
  }
  * { box-sizing: border-box; margin: 0; padding: 0; }
  html, body { width: 1200px; height: 933px; overflow: hidden; }
  body { background: var(--backdrop); position: relative; }

  .card {
    position: absolute;
    left: 274px;
    width: 653px;
    height: 374px;
    overflow: hidden;
    box-shadow: 0 4px 14px rgba(0,0,0,0.18);
  }
  .card--front { top: 64px; background: var(--paper); }
  .card--back { top: 494px; background: var(--mid-blue); }

  .company-name {
    position: absolute;
    left: 0; right: 0;
    text-align: center;
    font-family: "Tinos", "Times New Roman", serif;
    font-weight: 700;
    font-size: 39px;
    letter-spacing: 0.2px;
    white-space: nowrap;
  }
  .card--front .company-name { top: 70px; color: var(--navy); }
  .card--back .company-name { top: 161px; color: var(--paper); font-weight: 400; font-size: 41px; }

  .holder { position: absolute; left: 35px; top: 194px; }
  .holder__name {
    font-family: "Tinos", "Times New Roman", serif;
    font-size: 32px;
    font-weight: 400;
    color: var(--ink);
    line-height: 34px;
    white-space: nowrap;
  }
  .holder__role {
    font-family: "Arimo", Arial, sans-serif;
    font-size: 24px;
    font-weight: 500;
    color: var(--ink);
    line-height: 24px;
  }

  .divider {
    position: absolute;
    left: 306px; top: 174px;
    width: 2px; height: 98px;
    background: var(--ink);
  }

  .contacts { position: absolute; left: 321px; top: 174px; list-style: none; }
  .contacts li {
    display: flex;
    align-items: center;
    height: 26px;
    font-family: "Arimo", Arial, sans-serif;
    font-size: 18.5px;
    color: var(--ink);
    white-space: nowrap;
  }
  .contacts svg { width: 13px; height: 13px; margin-right: 15px; flex: none; }

  .wave { position: absolute; left: 0; bottom: 0; width: 653px; height: 60px; }
</style>
</head>
<body>
  <section class="card card--front">
    <h1 class="company-name">Bramblefield Growth Partners</h1>

    <div class="holder">
      <p class="holder__name">Malcolm Dervaney</p>
      <p class="holder__role">Owner</p>
    </div>

    <div class="divider"></div>

    <ul class="contacts">
      <li>
        <svg viewBox="0 0 13 13" aria-hidden="true"><rect width="13" height="13" fill="#0355a3"/><path d="M3 5 Q6.5 2.5 10 5 L9 6 L7.8 5.2 H5.2 L4 6 Z M4 7 H9 V10 H4 Z" fill="#fff"/></svg>
        0418923047
      </li>
      <li>
        <svg viewBox="0 0 13 13" aria-hidden="true"><rect width="13" height="13" fill="#0355a3"/><rect x="3" y="4" width="7" height="5" fill="#fff"/><path d="M3 4 L6.5 7 L10 4" stroke="#0355a3" fill="none" stroke-width="0.9"/></svg>
        malcolm@bgp.com.au
      </li>
      <li>
        <svg viewBox="0 0 13 13" aria-hidden="true"><rect width="13" height="13" fill="#0355a3"/><circle cx="6.5" cy="6.5" r="3.6" fill="none" stroke="#fff" stroke-width="1.1"/><path d="M2.9 6.5 H10.1 M6.5 2.9 V10.1" stroke="#fff" stroke-width="0.8"/></svg>
        bramblefieldgrowth.com.au
      </li>
      <li>
        <svg viewBox="0 0 13 13" aria-hidden="true"><rect width="13" height="13" fill="#0355a3"/><path d="M6.5 2.6 A2.6 2.6 0 0 1 9.1 5.2 C9.1 7 6.5 10.2 6.5 10.2 C6.5 10.2 3.9 7 3.9 5.2 A2.6 2.6 0 0 1 6.5 2.6 Z" fill="#fff"/><circle cx="6.5" cy="5.2" r="1" fill="#0355a3"/></svg>
        58 Quorrin Ct, Elmbridge Vic 3190
      </li>
    </ul>

    <svg class="wave" viewBox="0 0 653 60" preserveAspectRatio="none" aria-hidden="true">
      <path d="M50 27 Q330 -8 653 17 L653 24 Q330 -2 50 27 Z" fill="#3176b5"/>
      <path d="M0 38 Q330 2 653 30 L653 60 L0 60 Z" fill="#0355a3"/>
    </svg>
  </section>

  <section class="card card--back">
    <h2 class="company-name">Bramblefield Growth Partners</h2>
  </section>
</body>
</html>
```